ambitious event and festival agency from austria needs fresh business card design

A new design is due for the new headquarters and the new challenges. We organize events for different target groups from 16 to 60 years. The design should therefore be straightforward and not confused, so we are open to new colors and the logo may also be changed. In general, however, the most interesting suggestions are the most interesting ones. after this order we are looking for more graphics for brightloom facebook instagramm homepage etc A new design is due for the new headquarters and the new challenges. We organize events for different target groups from 16 to 60 years. The design should therefore be straightforward and not confused, so we are open to new colors and the logo may also be changed. In general, however, the most interesting suggestions are the most interesting ones. after this order we are looking for more graphics for brightloom facebook instagramm homepage etc A new design is due for the new headquarters and the new challenges. We organize events for different target groups from 16 to 60 years. The design should therefore be straightforward and not confused, so we are open to new colors and the logo may also be changed. In general, however, the most interesting suggestions are the most interesting ones. after this order we are looking for more graphics for brightloom facebook instagramm homepage etc
Updates

Reason: I am sorry for this decision but i need some more time. No new designs please, there are so many good ones and I will have made a decision in the next 3 days.

Target Market(s)

Industry/Entity Type

Business

Font styles to use
Serif
Sans Serif

Colors

Designer to choose colors to be used in the design.

Requirements
Must have
Nice to have
Should not have

```html
<!DOCTYPE html>
<html lang="en">
<head>
<meta charset="utf-8">
<title>brightloom business card</title>
<link rel="stylesheet" href="https://fonts.googleapis.com/css2?family=Open+Sans:wght@400;600;700&display=swap">
<style>
  :root {
    --backdrop: #3a322d;
    --card: #111111;
    --card-edge: #1c1c1c;
    --accent: #d1323f;
    --ink: #f2f2f2;
    --silver: #c9c9c9;
    --rule: #262626;
  }
  * { margin: 0; padding: 0; box-sizing: border-box; }
  html, body {
    width: 1200px; height: 900px; overflow: hidden;
    background: var(--backdrop);
    font-family: "Open Sans", sans-serif;
  }
  .canvas {
    position: relative; width: 1200px; height: 900px;
    display: flex; align-items: center; justify-content: center; gap: 50px;
  }
  .card {
    position: relative; width: 525px; height: 300px;
    background: var(--card);
    border: 1px solid var(--card-edge);
    box-shadow: 0 10px 30px rgba(0,0,0,0.45);
  }
  .card-front .mark-block {
    position: absolute; left: 70px; top: 105px;
    width: 90px; height: 90px; background: var(--accent);
  }
  .card-front .divider {
    position: absolute; left: 232px; top: 40px; bottom: 40px;
    width: 1px; background: var(--rule);
  }
  .contact {
    position: absolute; left: 262px; top: 62px;
    color: var(--ink); font-size: 14px; line-height: 1.35;
  }
  .contact .person-name {
    color: var(--accent); font-weight: 700; font-size: 19px; line-height: 1.2;
  }
  .contact .person-role { font-size: 13.5px; margin-bottom: 16px; }
  .contact .address { margin-bottom: 14px; }
  .contact .line { display: flex; align-items: center; gap: 8px; }
  .contact .line svg { width: 11px; height: 11px; fill: var(--accent); flex: none; }
  .card-back { display: flex; align-items: center; justify-content: center; }
  .wordmark {
    color: var(--silver); font-size: 46px; font-weight: 600; letter-spacing: -0.5px;
  }
</style>
</head>
<body>
<main class="canvas">
  <section class="card card-front">
    <div class="mark-block" aria-hidden="true"></div>
    <div class="divider"></div>
    <div class="contact">
      <p class="person-name">Lukas Berger</p>
      <p class="person-role">Managing Director</p>
      <p class="address">12345, Address Goes Here<br>Country Name, 123456.</p>
      <p class="line">
        <svg viewBox="0 0 12 12"><path d="M2.5 0.8 4.4 3.2 3.3 4.6c.7 1.6 2 2.9 3.6 3.7l1.4-1.1 2.4 1.9-1.1 1.9C5.5 10.6 1.2 6.4.6 2z"/></svg>
        043-512 874 300
      </p>
      <p class="line">
        <svg viewBox="0 0 12 12"><path d="M0 2h12v1.2L6 7 0 3.2z M0 4.6 6 8.4l6-3.8V10H0z"/></svg>
        info@brightloom.at
      </p>
      <p class="line">
        <svg viewBox="0 0 12 12"><path d="M5 3.5 7 1.5a2.4 2.4 0 0 1 3.5 3.5L8.5 7 7.6 6.1l2-2A1.1 1.1 0 0 0 8 2.4L5.9 4.4z M7 8.5 5 10.5A2.4 2.4 0 0 1 1.5 7L3.5 5l.9.9-2 2A1.1 1.1 0 0 0 4 9.6l2.1-2z M3.8 7.3 7.3 3.8l.9.9-3.5 3.5z"/></svg>
        www.brightloom.at
      </p>
    </div>
  </section>
  <section class="card card-back">
    <p class="wordmark">brightloom</p>
  </section>
</main>
</body>
</html>
```